SkyvornQ Business Cards and Stationary Design

Need a design for our business cards and stationary. I want to carry on the theme of the logo. I want the business cards to have a design on the back. I would like the business cards and the stationary to carry the same theme, design scheme, and branding

Target Market(s)

Airlines and Maintenance Facilities

Industry/Entity Type

Aviation

Contact Information for Business Card

Name
Position Title
Address: 4827 Trellis Hollow Road, Fort Pierce, Florida, 34951
Office Number
Mobile Number
Email
Website

Font styles to use
Serif
Sans Serif

Colors

Designer to choose colors to be used in the design.

```html
<!DOCTYPE html>
<html lang="en">
<head>
<meta charset="utf-8">
<title>SkyvornQ Business Card</title>
<link href="https://fonts.googleapis.com/css2?family=Open+Sans:wght@300;400;600;700&family=Open+Sans+Condensed:wght@700&display=swap" rel="stylesheet">
<style>
  :root {
    --navy: #0d2e6b;
    --navy-deep: #0a2358;
    --sky: #1a9be0;
    --blue: #1565b8;
    --ink: #1c2a48;
    --grey: #5a6272;
    --rule: #b9bec8;
    --paper: #ffffff;
    --backdrop: #e9ebef;
  }
  * { box-sizing: border-box; margin: 0; padding: 0; }
  html, body { width: 1200px; height: 872px; overflow: hidden; }
  body {
    background: var(--backdrop);
    font-family: "Open Sans", Arial, sans-serif;
    color: var(--ink);
    position: relative;
  }
  .card {
    position: absolute;
    width: 530px;
    height: 304px;
    background: var(--paper);
    box-shadow: 0 6px 18px rgba(20, 30, 60, 0.18);
    overflow: hidden;
  }
  /* Back of card */
  .card-back { left: 40px; top: 90px; }
  .card-back .mark-circle {
    position: absolute;
    left: 52px; top: 82px;
    width: 140px; height: 140px;
    border-radius: 50%;
    border: 9px solid var(--blue);
  }
  .card-back .brand {
    position: absolute;
    left: 225px; top: 118px;
    font-weight: 700;
    font-size: 38px;
    letter-spacing: 7px;
    color: var(--navy);
  }
  .card-back .brand-url {
    position: absolute;
    left: 230px; top: 172px;
    font-size: 14px;
    letter-spacing: 3px;
    color: var(--ink);
  }
  /* Front of card */
  .card-front { left: 630px; top: 470px; }
  .band {
    position: absolute;
    left: 0; top: 0;
    width: 100%; height: 92px;
    background: linear-gradient(90deg, var(--navy-deep) 0%, var(--blue) 30%, var(--sky) 50%, var(--blue) 70%, var(--navy-deep) 100%);
  }
  .band-rule {
    position: absolute;
    left: 0; top: 97px;
    width: 100%; height: 2px;
    background: var(--navy);
  }
  .front-circle {
    position: absolute;
    left: 225px; top: 55px;
    width: 80px; height: 80px;
    border-radius: 50%;
    background: var(--paper);
    border: 5px solid var(--blue);
  }
  .front-brand {
    position: absolute;
    left: 0; top: 148px;
    width: 100%;
    text-align: center;
    font-weight: 700;
    font-size: 30px;
    letter-spacing: 7px;
    color: var(--navy);
  }
  .holder {
    position: absolute;
    right: 285px; top: 206px;
    text-align: right;
  }
  .holder-name {
    font-family: "Open Sans Condensed", "Arial Narrow", sans-serif;
    font-weight: 700;
    font-size: 19px;
    color: var(--navy);
    line-height: 1.1;
  }
  .holder-title {
    font-weight: 300;
    font-size: 15px;
    color: var(--grey);
    letter-spacing: 0.5px;
    line-height: 1.3;
  }
  .holder-address {
    margin-top: 6px;
    font-size: 10.5px;
    line-height: 1.35;
    color: var(--ink);
    display: flex;
    align-items: flex-start;
    justify-content: flex-end;
    gap: 5px;
  }
  .divider {
    position: absolute;
    left: 260px; top: 205px;
    width: 1px; height: 80px;
    background: var(--rule);
  }
  .contact-list {
    position: absolute;
    left: 276px; top: 205px;
    list-style: none;
  }
  .contact-list li {
    display: flex;
    align-items: center;
    gap: 6px;
    font-size: 12px;
    line-height: 20px;
    color: var(--ink);
  }
  .icon { width: 12px; height: 12px; flex: none; }
  .holder-address .icon { margin-top: 1px; }
</style>
</head>
<body>

<section class="card card-back" aria-label="Card back">
  <div class="mark-circle"></div>
  <div class="brand">SKYVORNQ</div>
  <div class="brand-url">www.skyvornq.com</div>
</section>

<section class="card card-front" aria-label="Card front">
  <div class="band"></div>
  <div class="band-rule"></div>
  <div class="front-circle"></div>
  <div class="front-brand">SKYVORNQ</div>

  <div class="holder">
    <div class="holder-name">DORIAN HALVERS</div>
    <div class="holder-title">PRESIDENT</div>
    <div class="holder-address">
      <svg class="icon" viewBox="0 0 12 12"><circle cx="6" cy="6" r="5.3" fill="none" stroke="#1565b8" stroke-width="1.2"/><path d="M6 2.8a2 2 0 0 1 2 2c0 1.5-2 3.8-2 3.8S4 6.3 4 4.8a2 2 0 0 1 2-2z" fill="#1565b8"/></svg>
      <span>4827 Trellis Hollow Road, Fort Pierce,<br>Florida, 34951</span>
    </div>
  </div>

  <div class="divider"></div>

  <ul class="contact-list">
    <li>
      <svg class="icon" viewBox="0 0 12 12"><circle cx="6" cy="6" r="5.3" fill="none" stroke="#1565b8" stroke-width="1.2"/><path d="M4 3.2l1 1.2-.6.8c.4.9 1 1.5 1.9 1.9l.8-.6 1.2 1-.6 1C5.8 8.6 3.4 6.2 3.2 4.2z" fill="#1565b8"/></svg>
      <span>772-555-0148</span>
    </li>
    <li>
      <svg class="icon" viewBox="0 0 12 12"><circle cx="6" cy="6" r="5.3" fill="none" stroke="#1565b8" stroke-width="1.2"/><rect x="4.2" y="3" width="3.6" height="6" rx="0.6" fill="none" stroke="#1565b8" stroke-width="1"/></svg>
      <span>772-555-0193</span>
    </li>
    <li>
      <svg class="icon" viewBox="0 0 12 12"><circle cx="6" cy="6" r="5.3" fill="none" stroke="#1565b8" stroke-width="1.2"/><rect x="3.2" y="4" width="5.6" height="4" fill="none" stroke="#1565b8" stroke-width="0.9"/><path d="M3.2 4l2.8 2.2L8.8 4" fill="none" stroke="#1565b8" stroke-width="0.9"/></svg>
      <span>info@skyvornq.com</span>
    </li>
    <li>
      <svg class="icon" viewBox="0 0 12 12"><circle cx="6" cy="6" r="5.3" fill="none" stroke="#1565b8" stroke-width="1.2"/><ellipse cx="6" cy="6" rx="2" ry="5" fill="none" stroke="#1565b8" stroke-width="0.8"/><path d="M1 6h10" stroke="#1565b8" stroke-width="0.8"/></svg>
      <span>www.skyvornq.com</span>
    </li>
  </ul>
</section>

</body>
</html>
```